Marrowind - IT Consultancy Website

Our company is called Marrowind and our purpose is to help companies sustainably embrace and reap the benefits of cloud platforms, through transforming practices, skills and technology using DevOps and Security practices such that they are able to automate, manage and secure their cloud platforms to deliver product to market with increasing velocity.

To get our business started I require a website that will model the typical layout of an IT consultancy services company to an Australian Market. There are many examples of such a site, here are some of them. We would like a landing page and then a few simple menu options (About, Blog, Services etc..) to additional content

http://pelvo.com.au/
http://www.brisket.com.au/
http://www.tandu.com.au/

I require the site to be created with a separate CSS file that maintains the colour palette. This is a very important requirement, I want to be able to change the colours employed in the site in a single location and not have to scan through multiple files to replace the codes.

The website must be built using static content as it will not be hosted on a web server but instead in QNT using S3 and CloudFront CDN. Therefore please stick to HTML, JavaScript, CSS and other static file formats. The website needs to be response, smooth and reactive. It should render on desktop, mobile and tablet and feature smooth scrolling, transitions and fade in's.

The website should give the customer confidence that they are dealing with a highly professional IT services company, focused strongly on cloud (QNT, Vantrel Skyline, Horvik Vapor etc..), motivated by beautiful and fluid design.

In order to make this simpler for you, the designer, I have already purchased this template from https://skinmarketly.com/theme/the-venture-allround-template-KX7Q41093 and uploaded it. Feel free to use this template if you choose (note that it makes use of a separate color palette which is a key requirement) or use one of your own choosing. If you do use this template ensure that it does not look too much like "another bootstrap site" therefore use the layout and widgets but make the site look fresh and original too.
Obviously you must delete all trace of the bootstrap package once the project has completed if you do use it

Target Market(s)

Corporate and medium enterprise businesses

Industry/Entity Type

Information Technology

Coding

Coded - Design and coding required

Number of Pages Required

4 page

Font styles to use
Sans Serif

Colors
abd036
33a6d7

Requirements
Must have
• The website should give the customer confidence that they are dealing with a highly professional IT services company, focused strongly on cloud (QNT, Vantrel Skyline, Horvik Vapor etc..), motivated by beautiful and fluid design. Our company name is Marrowind, the site needs to pay homage to the themes of fluidity and logic
• Along with About Us, Services and a Blog page could I also get social logo's included too
Nice to have
• The website must be built using static content as it will not be hosted on a web server but instead in QNT using S3 and CloudFront CDN. Therefore please stick to HTML, JavaScript, CSS and other static file formats. The website needs to be response, smooth and reactive. It should render on desktop, mobile and tablet and feature smooth scrolling, transitions and fade in's.
Should not have
• Lurid colours, or too much animations. The design must "flow"

```html
<!DOCTYPE html>
<html lang="en">
<head>
<meta charset="utf-8">
<title>Marrowind IT Consultancy</title>
<link rel="stylesheet" href="https://fonts.googleapis.com/css2?family=Open+Sans:ital,wght@0,400;0,600;0,700;1,400;1,600&display=swap">
<style>
:root{
  --blue:#1fa3db;
  --blue-dark:#1787bd;
  --orange:#e2842f;
  --orange-dark:#c96f20;
  --ink:#333333;
  --text:#6b6b6b;
  --muted:#9a9a9a;
  --line:#e4e4e4;
  --white:#ffffff;
  --footer:#3b3b3b;
  --footer-bottom:#2f2f2f;
  --footer-text:#c9c9c9;
}
*{box-sizing:border-box;margin:0;padding:0}
html,body{width:1200px;height:2965px;overflow:hidden}
body{font-family:"Open Sans",Arial,sans-serif;color:var(--text);background:var(--white);position:relative}
a{text-decoration:none}
.abs{position:absolute}
section,header,footer{position:absolute;left:0;width:1200px}

/* header */
.site-header{top:0;height:122px;border-top:4px solid var(--blue);background:var(--white)}
.brand{left:97px;top:34px;font-size:27px;font-weight:700;color:var(--blue);line-height:1;letter-spacing:.5px}
.search{left:745px;top:28px;width:30px;height:30px;border-radius:50%;background:#f2ede8}
.social-label{left:789px;top:36px;font-size:10.5px;color:var(--muted)}
.social-dots{left:974px;top:28px;display:flex;gap:6px}
.social-dots span{width:28px;height:28px;border-radius:50%;background:var(--blue)}
.social-dots span.alt{background:#3aa5dc}
.social-dots span.warm{background:var(--orange)}
.social-dots span.deep{background:#1b7fa8}
.main-nav{right:88px;top:82px;display:flex}
.main-nav a{font-size:11px;color:var(--ink);text-transform:uppercase;padding:0 0 0 60px}
.main-nav a.active{color:var(--blue)}

/* hero */
.hero{top:122px;height:490px}
.hero-photo{position:absolute;inset:0;background:linear-gradient(180deg,#b9c8d3 0%,#8fa3b3 45%,#5c6b78 70%,#2f3a44 100%)}
.hero-title{left:320px;top:180px;width:560px;height:62px;background:rgba(31,163,219,.9);color:var(--white);font-size:33px;font-weight:700;text-align:center;line-height:62px;text-transform:uppercase}
.hero-sub{left:392px;top:250px;width:418px;height:58px;background:rgba(31,163,219,.9);color:var(--white);font-size:31px;font-style:italic;text-align:center;line-height:58px;text-transform:uppercase}
.hero-arrow{top:333px;width:30px;height:30px;border-radius:50%;background:rgba(60,60,60,.75)}

/* welcome */
.welcome{top:612px;height:476px}
.section-title{position:absolute;left:0;width:1200px;text-align:center;font-size:24px;font-weight:700;color:var(--ink);text-transform:uppercase}
.welcome .section-title{top:60px}
.welcome-copy{left:99px;top:124px;width:506px;font-size:11.4px;line-height:25px;color:#666}
.welcome-copy p+p{margin-top:14px}
.btn{display:inline-block;color:var(--white);font-size:11px;font-weight:700;text-transform:uppercase;text-align:center;border-radius:2px}
.btn-orange{background:var(--orange);border-bottom:3px solid var(--orange-dark)}
.btn-blue{background:var(--blue);border-bottom:3px solid var(--blue-dark)}
.welcome .btn{position:absolute;left:99px;top:368px;width:134px;height:44px;line-height:42px}
.welcome-photo{left:655px;top:128px;width:446px;height:286px;border:1px solid var(--line);padding:10px;background:var(--white)}
.welcome-photo div{width:100%;height:100%;background:linear-gradient(135deg,#dfe4e8 0%,#9aa6b1 50%,#2b3a55 100%)}

/* services */
.services{top:1088px;height:478px;background:linear-gradient(180deg,#23a4dc 0%,#1b95cc 60%,#1589c0 100%)}
.services .section-title{top:64px;color:var(--white)}
.service-card{top:189px;width:312px;height:206px;border:1px solid rgba(255,255,255,.8);text-align:center;color:var(--white)}
.service-icon{position:absolute;left:86px;top:-72px;width:140px;height:140px;border-radius:50%;background:var(--white);border:7px solid rgba(255,255,255,.45);background-clip:padding-box;display:flex;align-items:center;justify-content:center}
.service-name{position:absolute;top:96px;width:100%;font-size:13px;font-weight:700;text-transform:uppercase}
.service-text{position:absolute;top:118px;left:30px;width:250px;font-size:11px;line-height:21px;color:#e8f5fb}
.service-more{position:absolute;top:166px;width:100%;font-size:10px;font-weight:700;text-transform:uppercase}

/* why choose */
.why{top:1566px;height:599px}
.why .section-title{top:64px}
.why-lead{left:230px;top:108px;width:740px;text-align:center;font-size:12.5px;line-height:27px;color:var(--muted)}
.why-photo{left:99px;top:180px;width:346px;height:350px}
.why-list{left:557px;top:196px;width:500px}
.why-item{position:relative;height:95px;padding-left:88px}
.why-icon{position:absolute;left:0;top:6px;width:60px;height:60px;border-radius:50%;border:1px solid #e3d7cc;display:flex;align-items:center;justify-content:center}
.why-item h3{font-size:14px;font-weight:400;color:var(--orange);margin-bottom:7px}
.why-item p{font-size:11px;line-height:22px;color:#777;width:420px}
.why-scroll{left:1091px;top:196px;width:6px;height:266px;background:#ececec}
.why-scroll span{position:absolute;left:0;top:156px;width:6px;height:44px;background:#555}
.why-btns{left:569px;top:478px;display:flex;gap:8px}
.why-btns .btn{width:119px;height:40px;line-height:38px}

/* testimonials */
.testimonials{top:2165px;height:352px;background:linear-gradient(90deg,rgba(226,132,47,.95) 0%,rgba(234,148,64,.9) 50%,rgba(226,132,47,.95) 100%),#d6883d}
.testimonials .section-title{top:70px;color:var(--white)}
.avatar{left:198px;top:148px;width:130px;height:130px;border-radius:50%;background:linear-gradient(180deg,#e9e3dc,#b9a89a);border:5px solid var(--white)}
.quote-badge{left:288px;top:128px;width:46px;height:46px;border-radius:50%;background:var(--blue);border:4px solid var(--white);display:flex;align-items:center;justify-content:center;color:var(--white);font-size:34px;font-weight:700;line-height:1}
.quote-text{left:405px;top:150px;width:600px;font-size:12px;font-style:italic;line-height:25px;color:var(--white)}
.quote-author{left:405px;top:240px;font-size:11px;color:var(--white)}
.quote-author b{font-weight:700}
.slide-arrow{top:188px;color:rgba(255,255,255,.8);font-size:22px}

/* clients */
.clients{top:2517px;height:162px;display:flex;align-items:center;justify-content:center}
.client{display:flex;align-items:center;gap:8px;font-size:14px;font-weight:700;color:#555;width:138px;justify-content:center}
.client i{width:14px;height:14px;border-radius:50%;background:var(--orange);display:inline-block}

/* footer */
.site-footer{top:2679px;height:237px;background:var(--footer);color:var(--footer-text)}
.foot-col{top:46px}
.foot-col h4{font-size:13px;font-weight:700;color:var(--white);text-transform:uppercase;margin-bottom:12px}
.foot-col li{list-style:none;font-size:11px;line-height:22.5px}
.foot-col p{font-size:11px;line-height:21px}
.news-input{margin-top:14px;width:228px;height:36px;background:#4b4b4b;border:1px solid #555;font-size:10.5px;padding-left:10px;line-height:34px;color:#bbb}
.news-btn{margin-top:8px;width:117px;height:36px;line-height:34px;font-size:11px}
.contact-line{display:flex;align-items:center;gap:10px}
.follow li{display:flex;align-items:center;gap:8px;line-height:27px}
.follow i{width:24px;height:24px;border-radius:50%;background:#676767;display:inline-block}
.footer-bottom{top:2916px;height:49px;background:var(--footer-bottom);color:#9c9c9c;font-size:10px;text-align:center;line-height:49px;text-transform:uppercase}
</style>
</head>
<body>

<header class="site-header">
  <div class="abs brand">MARROWIND</div>
  <div class="abs search">
    <svg width="30" height="30" viewBox="0 0 30 30"><circle cx="14" cy="14" r="4.5" fill="none" stroke="#e2842f" stroke-width="2"/><line x1="17.5" y1="17.5" x2="21" y2="21" stroke="#e2842f" stroke-width="2"/></svg>
  </div>
  <div class="abs social-label">Connect with our social network :</div>
  <div class="abs social-dots"><span class="deep"></span><span class="alt"></span><span class="warm"></span><span class="deep"></span></div>
  <nav class="abs main-nav">
    <a class="active" href="#">Home</a><a href="#">About Us</a><a href="#">Services</a><a href="#">Testimonials</a><a href="#">Blog</a><a href="#">Contact Us</a>
  </nav>
</header>

<section class="hero">
  <div class="hero-photo" role="img" aria-label="Office desk with laptop overlooking a city skyline"></div>
  <div class="abs hero-title">Marrowind IT Consultancy</div>
  <div class="abs hero-sub">Skills and Technology</div>
  <div class="abs hero-arrow" style="left:565px"><svg width="30" height="30"><path d="M17 9l-6 6 6 6" fill="none" stroke="#fff" stroke-width="2.5"/></svg></div>
  <div class="abs hero-arrow" style="left:603px"><svg width="30" height="30"><path d="M13 9l6 6-6 6" fill="none" stroke="#fff" stroke-width="2.5"/></svg></div>
</section>

<section class="welcome">
  <h2 class="section-title">Welcome to Marrowind IT Consultancy</h2>
  <div class="abs welcome-copy">
    <p>Neque porro quisquam est, qui dolorem ipsum quia dolor sit amet, consectetur, adipisci velitera, sed quia non numquam eius modi tempora incidunt ut labore et dolore magnam aliquam quaerat voluptatem. Ut enim ad minima veniam, quis nostrum exercitationemtempora incidunt ut voluptate velit esse quam nostrum exercitationem...</p>
    <p>Sed quia non numquam eius modi tempora incidunt ut labore et dolore magnam aliquam quaerat voluptatem. Ut enim ad minima veniam, quis nostrum exercitationemtempora incidunt ut labore et dolore magnam aliquam quaerat voluptatem. Ut enim ad minima veniam, quis voluptate velit esse quam nostrum exercitationem...</p>
  </div>
  <a class="btn btn-orange" href="#">Read More Info</a>
  <div class="abs welcome-photo"><div role="img" aria-label="Two consultants in a meeting at an office desk"></div></div>
</section>

<section class="services">
  <h2 class="section-title">Our Services</h2>
  <div class="abs service-card" style="left:99px">
    <div class="service-icon"><svg width="70" height="70" viewBox="0 0 70 70" fill="none" stroke="#1fa3db" stroke-width="5" stroke-linejoin="round"><path d="M35 6l16 8-16 8-16-8z"/><path d="M19 14v16l16 8V22M51 14v16l-16 8"/><path d="M18 34l16 8-16 8-16-8z" transform="translate(1 4)"/><path d="M52 34l16 8-16 8-16-8z" transform="translate(-1 4)"/><path d="M3 46v14l16 8V54M51 54v14l16-8V46"/></svg></div>
    <div class="service-name">QNT</div>
    <div class="service-text">Nemo enim ipsam voluptatem quia voluptas sit aspernatur aut odit aut fugit, sed quia...</div>
    <div class="service-more">Read More &#10230;</div>
  </div>
  <div class="abs service-card" style="left:443px">
    <div class="service-icon"><svg width="64" height="64" viewBox="0 0 64 64"><rect x="8" y="8" width="48" height="48" rx="6" fill="#1fa3db"/></svg></div>
    <div class="service-name">Vantrel Skyline</div>
    <div class="service-text">Nemo enim ipsam voluptatem quia voluptas sit aspernatur aut odit aut fugit, sed quia...</div>
    <div class="service-more">Read More &#10230;</div>
  </div>
  <div class="abs service-card" style="left:787px">
    <div class="service-icon"><svg width="84" height="60" viewBox="0 0 84 60"><path d="M20 54a16 16 0 0 1-2-32 22 22 0 0 1 42-6 18 18 0 0 1 6 38z" fill="#1fa3db"/></svg></div>
    <div class="service-name">Horvik Vapor</div>
    <div class="service-text">Nemo enim ipsam voluptatem quia voluptas sit aspernatur aut odit aut fugit, sed quia...</div>
    <div class="service-more">Read More &#10230;</div>
  </div>
</section>

<section class="why">
  <h2 class="section-title">Why Choose Us</h2>
  <p class="abs why-lead">Simplemente el texto de relleno de las imprentas y archivos de texto. Lorem Ipsum ha sido el texto de relleno estándar de las industrias desde voluptatem sequi nesciunt.</p>
  <div class="abs why-photo" role="img" aria-label="Desktop monitor showing a team in a business meeting" style="background:linear-gradient(180deg,#dfe3e6 0%,#c4ccd3 55%,#e9ebed 100%)"></div>
  <div class="abs why-list">
    <div class="why-item">
      <div class="why-icon"><svg width="26" height="26" viewBox="0 0 26 26" fill="none" stroke="#e2842f" stroke-width="2.5"><circle cx="13" cy="13" r="10"/><circle cx="13" cy="13" r="4"/></svg></div>
      <h3>Nemo enim ipsam voluptatem quia volupta</h3>
      <p>Lorem Ipsum is simply dummy text of the printing and typesetting industry. Lorem Ipsum has been the industry's...</p>
    </div>
    <div class="why-item">
      <div class="why-icon"><svg width="28" height="24" viewBox="0 0 28 24" fill="#e2842f"><circle cx="14" cy="6" r="4"/><circle cx="5" cy="9" r="3"/><circle cx="23" cy="9" r="3"/><path d="M7 22c0-5 3-8 7-8s7 3 7 8zM0 22c0-4 2-6 5-6s4 2 4 2l-2 4zM28 22c0-4-2-6-5-6s-4 2-4 2l2 4z"/></svg></div>
      <h3>Nemo enim ipsam voluptatem quia volupta</h3>
      <p>Lorem Ipsum is simply dummy text of the printing and typesetting industry. Lorem Ipsum has been the industry's...</p>
    </div>
    <div class="why-item">
      <div class="why-icon"><svg width="28" height="26" viewBox="0 0 28 26" fill="none" stroke="#e2842f" stroke-width="2.5"><circle cx="10" cy="14" r="5" stroke-dasharray="3 2"/><circle cx="10" cy="14" r="2"/><circle cx="21" cy="7" r="4" stroke-dasharray="2.5 1.5"/></svg></div>
      <h3>Nemo enim ipsam voluptatem quia volupta</h3>
      <p>Lorem Ipsum is simply dummy text of the printing and typesetting industry. Lorem Ipsum has been the industry's...</p>
    </div>
  </div>
  <div class="abs why-scroll"><span></span></div>
  <div class="abs why-btns"><a class="btn btn-orange" href="#">Read More</a><a class="btn btn-blue" href="#">Start Today</a></div>
</section>

<section class="testimonials">
  <h2 class="section-title">Testimonials</h2>
  <div class="abs slide-arrow" style="left:100px">&#8592;</div>
  <div class="abs slide-arrow" style="left:1082px">&#8594;</div>
  <div class="abs avatar" role="img" aria-label="Client portrait"></div>
  <div class="abs quote-badge">&#8221;</div>
  <p class="abs quote-text">&#8220; &nbsp;Nemo enim ipsam voluptatem quia voluptas sit aspernatur aut odit aut fugit, sed quia consequuntur magni dolores eos qui ratione voluptatem sequi nesciunt. Neque porro quisquam est, qui dolorem ipsum quia dolor sit amet, consectetur, adipisci velit, sed quia non numquam... &#8221;</p>
  <div class="abs quote-author"><b>-JOHN DOE /</b> Our Client</div>
</section>

<section class="clients">
  <div class="client"><i></i>lumora</div>
  <div class="client"><i></i>tessly</div>
  <div class="client"><i></i>Pine Ridge Tech</div>
  <div class="client"><i></i>Corvan Hale</div>
  <div class="client"><i></i>la maisonne</div>
  <div class="client"><i></i>giftora</div>
  <div class="client"><i></i>nuvesta</div>
</section>

<footer class="site-footer">
  <div class="abs foot-col" style="left:99px">
    <h4>Welcome</h4>
    <ul><li>Home</li><li>About us</li><li>Services</li><li>Blog</li><li>Testimonials</li><li>Contact us</li></ul>
  </div>
  <div class="abs foot-col" style="left:239px">
    <h4>Information</h4>
    <ul><li>Terms &amp; Conditions</li><li>Privacy Policy</li><li>Site Map</li><li>Disclaimer</li><li>FAQ</li></ul>
  </div>
  <div class="abs foot-col" style="left:415px;width:250px">
    <h4>Newsletter</h4>
    <p>Nemo enim ipsam voluptatem quia voluptas sit aspernatur aut odit aut fugit...</p>
    <div class="news-input">Enter E-mail</div>
    <div class="btn btn-blue news-btn">Subscribe</div>
  </div>
  <div class="abs foot-col" style="left:718px;width:250px">
    <h4>Contact Info</h4>
    <p style="text-transform:uppercase">Marrowind IT Consultancy</p>
    <p style="margin-top:6px">120 Street Name, State name,<br>Country name, Zip code : 2350 3652.</p>
    <p class="contact-line" style="margin-top:4px"><svg width="10" height="14" viewBox="0 0 10 14"><rect x="1" y="0.5" width="8" height="13" rx="1.5" fill="none" stroke="#c9c9c9"/></svg>Phone : ( +111) 888-8888</p>
    <p class="contact-line"><svg width="12" height="9" viewBox="0 0 12 9"><rect x="0.5" y="0.5" width="11" height="8" fill="none" stroke="#c9c9c9"/><path d="M1 1l5 4 5-4" fill="none" stroke="#c9c9c9"/></svg>info@Marrowind IT Consultancy.com</p>
  </div>
  <div class="abs foot-col follow" style="left:996px">
    <h4>Contact Info</h4>
    <ul><li><i></i>: Friendline</li><li><i></i>: Circlepost</li><li><i></i>: Chirpnet</li><li><i></i>: Workweave</li></ul>
  </div>
</footer>
<div class="abs footer-bottom" style="left:0;width:1200px">© 2016, Marrowind IT Consultancy. All rights reserved.</div>

</body>
</html>
```